A Techincal Author needs a site to promote his Programming Books

The StudyAlong series is a collection of books focusing on building the same app with different technologies. The purpose of this project is to design a web site home page that can be used to sell the books.

Expected Deliverables
• StudyAlong Logo as Illustrator file
• Master graphic design files for any relevant web assets
• HTML and CSS for home page, if applicable

Target Market(s)

The target market for our series is web programmers. They are people who have some experience, but want to learn a new tool. Programmers are analytical, logical people who like structure in the things they do.

Here are some things our customers like:

• Chirply / Postbox
• Crown of Ashes / Hollow Tide / Salt Hollow
• SmartPhones, Tablets, Stridelets, and other tech gadgets.

The design should try to speak to that market.

Requirements
Must have
• The primary tasks for this project are:
• 1) Create "Study Along" Logo.
• * All “NetPivot” properties use a similar logo approach, with the NetPivot ball icon on the left, a reflection below it. The company name is on the right, roughly the same size as the ball icon. A tag line underneath the company name, roughly the same size as the reflection.
• * Company Name: Study Along
• * Tagline: Knowledge to Boost Your Career
• * Logo color is up to the discretion of the designer, but should be compatible with the site design.
• * Sample Logos for other NetPivot properties in Illustrator format are available as attachments to this project.
• 2) Design the Study Along Home Page.
• The home page should follow this format:
• * Logo
• * Nav Bar
• • Buy (The Home Page)
• • About
• • Contact
• * Main Content
• • Home page content detailed in attachment
• * Footer
• • Copyright notice
• • Links to other stuff we do ( net-pivot.example | marlonpeake.example | BeyondTheGrid.example )
Nice to have
• It would be nice to have a book as part of the home page content.
Should not have
• Please do not use the same color scheme as BeyondTheGrid.example or Plumvane.example or QueryTheMaven.example

```html
<!DOCTYPE html>
<html lang="en">
<head>
<meta charset="utf-8">
<title>Study Along — Knowledge to Boost Your Career</title>
<link href="https://fonts.googleapis.com/css2?family=Open+Sans:wght@400;600;700;800&display=swap" rel="stylesheet">
<style>
:root{
  --ink:#1f1f1f;
  --muted:#555;
  --brand:#c8202a;
  --dark:#4a4a4a;
  --darker:#262626;
  --buy:#f05a5a;
  --publisher:#f7a11a;
  --line:#e2e2e2;
  --hero-bg:#ececec;
  --white:#fff;
}
*{box-sizing:border-box;margin:0;padding:0}
html,body{width:766px;height:1200px;overflow:hidden;background:var(--white)}
body{font-family:"Open Sans",Arial,sans-serif;color:var(--ink);position:relative}

.site-header{height:56px;display:flex;align-items:center;justify-content:space-between;padding:0 44px 0 84px;background:var(--white)}
.brand{display:flex;align-items:center;gap:7px}
.brand-dot{width:22px;height:22px;border-radius:50%;background:var(--brand)}
.brand-name{font-size:21px;font-weight:700;color:var(--brand);letter-spacing:-.3px}
.main-nav{display:flex;gap:22px}
.main-nav a{font-size:9px;font-weight:600;color:var(--ink);text-decoration:none;letter-spacing:.4px}

.hero{position:relative;height:276px;background:var(--hero-bg);overflow:hidden}
.hero-photo{position:absolute;left:300px;top:0;right:0;bottom:0;
  background:linear-gradient(90deg,#ececec 0%,#d9cfc4 25%,#b9a48f 55%,#8f8b86 100%)}
.hero-copy{position:absolute;left:95px;top:74px}
.hero-title{font-size:22px;font-weight:700;line-height:1.08;color:var(--ink);letter-spacing:.2px;text-transform:uppercase}
.signup{position:absolute;left:95px;top:126px;width:225px;background:rgba(255,255,255,.82);padding:9px 12px 11px}
.signup h2{font-size:9px;font-weight:600;letter-spacing:.3px;margin-bottom:7px}
.signup .field{height:17px;border:1px solid var(--line);background:var(--white);border-radius:9px;font-size:7px;color:#888;padding:3px 10px;margin-bottom:6px}
.signup .submit{width:100%;height:18px;border-radius:9px;background:var(--dark);color:var(--white);font-size:8px;font-weight:600;text-align:center;line-height:18px}

.welcome{text-align:center;padding-top:60px}
.welcome h2{font-size:16px;font-weight:800;letter-spacing:.3px}
.welcome p{width:500px;margin:9px auto 0;font-size:7px;line-height:1.55;color:var(--muted)}

.book{text-align:center;margin-top:18px}
.book h3{font-size:14px;font-weight:400;color:var(--ink)}
.sample-btn{display:inline-block;margin-top:6px;background:var(--darker);color:var(--white);font-size:6px;padding:3px 10px;border-radius:8px}
.price-table{width:480px;margin:13px auto 0;border-collapse:collapse;font-size:7px}
.price-table td{height:30px;border-bottom:2px solid var(--white)}
.price-table .option{width:200px;background:var(--dark);color:var(--white);font-weight:700;padding-left:12px}
.price-table .price{width:102px;background:#f4f4f4;text-align:center;font-size:13px;font-weight:600;color:var(--ink)}
.price-table .buy{width:94px;background:var(--buy);color:var(--white);text-align:center;font-size:6px}
.price-table .publisher{width:84px;background:var(--publisher);color:var(--white);text-align:center;font-size:6px}
.price-table .empty{background:#f4f4f4}

.partners{position:absolute;left:0;right:0;top:1072px;height:52px;display:flex;justify-content:center;align-items:center;gap:60px}
.partner-name{font-size:14px;font-weight:700;color:#2a3a6a}
.site-footer{position:absolute;left:0;right:0;bottom:0;height:64px;background:var(--darker);color:#bbb;font-size:7px;text-align:center;line-height:64px}
</style>
</head>
<body>
<header class="site-header">
  <div class="brand"><span class="brand-dot"></span><span class="brand-name">Study Along</span></div>
  <nav class="main-nav"><a href="#">HOME</a><a href="#">ABOUT US</a><a href="#">PRICING</a><a href="#">CONTACT</a></nav>
</header>

<section class="hero">
  <div class="hero-photo" role="img" aria-label="Photo of three people working together at a computer"></div>
  <div class="hero-copy"><h1 class="hero-title">Knowledge to<br>boost your career</h1></div>
  <form class="signup">
    <h2>SIGN UP FOR A FREE SAMPLE</h2>
    <div class="field">First Name</div>
    <div class="field">Email Address</div>
    <div class="submit">SUBMIT</div>
  </form>
</section>

<section class="welcome">
  <h2>WELCOME TO STUDY ALONG</h2>
  <p>Each book walks you through building the same practical app with a different framework, step by step. Learn the patterns, compare the tools, and grow the skills that move your career forward.</p>
</section>

<section class="book">
  <h3>Vertex 1.5 &amp; Scaffold</h3>
  <span class="sample-btn">View Sample</span>
  <table class="price-table">
    <tr><td class="option">With Mock Services</td><td class="price">$5.99</td><td class="buy">Buy From Us</td><td class="publisher">Buy From Publisher</td></tr>
    <tr><td class="option">With RuntimeJS Services</td><td class="price">$5.99</td><td class="buy">Buy From Us</td><td class="publisher">Buy From Publisher</td></tr>
    <tr><td class="option">With EmberScript Services</td><td class="price">$5.99</td><td class="buy">Buy From Us</td><td class="publisher">Buy From Publisher</td></tr>
    <tr><td class="option">Buy Them All</td><td class="price">$9.99</td><td class="buy">Buy From Us</td><td class="empty"></td></tr>
  </table>
</section>

<section class="book">
  <h3>Vertex 2 &amp; Scaffold</h3>
  <span class="sample-btn">View Sample</span>
  <table class="price-table">
    <tr><td class="option">With Mock Services</td><td class="price">$5.99</td><td class="buy">Buy From Us</td><td class="publisher">Buy From Publisher</td></tr>
    <tr><td class="option">With RuntimeJS Services</td><td class="price">$5.99</td><td class="buy">Buy From Us</td><td class="publisher">Buy From Publisher</td></tr>
    <tr><td class="option">With EmberScript Services</td><td class="price">$5.99</td><td class="buy">Buy From Us</td><td class="publisher">Buy From Publisher</td></tr>
    <tr><td class="option">Buy Them All</td><td class="price">$9.99</td><td class="buy">Buy From Us</td><td class="empty"></td></tr>
  </table>
</section>

<section class="book">
  <h3>Reactor</h3>
  <span class="sample-btn">View Sample</span>
  <table class="price-table">
    <tr><td class="option">With Mock Services</td><td class="price">$5.99</td><td class="buy">Buy From Us</td><td class="publisher">Buy From Publisher</td></tr>
    <tr><td class="option">With RuntimeJS Services</td><td class="price">$5.99</td><td class="buy">Buy From Us</td><td class="publisher">Buy From Publisher</td></tr>
    <tr><td class="option">With EmberScript Services</td><td class="price">$5.99</td><td class="buy">Buy From Us</td><td class="publisher">Buy From Publisher</td></tr>
    <tr><td class="option">Buy Them All</td><td class="price">$9.99</td><td class="buy">Buy From Us</td><td class="empty"></td></tr>
  </table>
</section>

<div class="partners">
  <span class="partner-name">Plumvane.example</span>
  <span class="partner-name">BeyondTheGrid.example</span>
</div>
<footer class="site-footer">© 2016 net-pivot.example</footer>
</body>
</html>
```